Looking for a dynamic business card for a pizzeria.

A business card with our food, logo, and space for name, title, email, website, phone. The card should convey quality, unique, amazing. On the front, I envision food photo or photos with the owners names and contact information. On the back, more food with locations, website, facebook, twitter, instagram icons. It should look polished, not cartoonish, or plain.
Target Market(s)
upscale, local food buyers, 30-50 years in age.
Industry/Entity Type
Restaurant
Contact Information for Business Card
Business Name: Bru'nettix, LLC
Website: www.brunettix.com
Back:
2 locations: (can list on the back of card)
1. Northvale
4087 Corlan Avenue
Larkport, OR 97412
360-481-5067
2. Cedar Rise
7315 Wendmere Road
Larkport, OR 97418
360-293-8840
front:
EDITABLE space for
Business name
Person's Name
title
2nd title
Email address
cell-phone number
Requirements
Must have
- logo
- my food photo or photos (no watermarks showing)
- locations on back
- Person contact information on front
- full bleed

```html
<!DOCTYPE html>
<html lang="en">
<head>
<meta charset="utf-8">
<title>Bru'nettix Business Card</title>
<link href="https://fonts.googleapis.com/css2?family=Arimo:wght@400;700&display=swap" rel="stylesheet">
<style>
  :root {
    --page: #e9e6e1;
    --red: #b3140f;
    --red-dark: #7d0d0b;
    --green: #2f5b2f;
    --green-dark: #224422;
    --white: #ffffff;
    --soft-white: #f1efec;
    --logo-green: #2d5a2d;
  }
  * { box-sizing: border-box; margin: 0; padding: 0; }
  html, body {
    width: 1200px; height: 950px; overflow: hidden;
    background: var(--page);
    font-family: "Arimo", Arial, sans-serif;
  }
  .sheet { position: relative; width: 1200px; height: 950px; }
  .card {
    position: absolute; left: 250px; width: 700px; height: 400px;
    overflow: hidden; box-shadow: 0 8px 24px rgba(0,0,0,.25);
  }
  .card-back { top: 45px; background: linear-gradient(100deg, var(--red) 0%, var(--red) 55%, var(--red-dark) 100%); }
  .card-front { top: 500px; background: linear-gradient(120deg, var(--green) 0%, var(--green-dark) 100%); }

  .social { position: absolute; top: 24px; right: 28px; display: flex; gap: 12px; }
  .social-dot { width: 16px; height: 16px; border-radius: 50%; background: var(--soft-white); }

  .back-mark {
    position: absolute; left: 300px; top: 155px;
    display: flex; align-items: center; gap: 14px;
  }
  .back-mark-name { font-size: 48px; font-weight: 700; color: var(--soft-white); letter-spacing: 1px; }
  .back-mark-dot { width: 30px; height: 30px; border-radius: 50%; background: var(--soft-white); }
  .back-web {
    position: absolute; left: 330px; bottom: 44px;
    font-size: 15px; letter-spacing: 3px; color: rgba(255,255,255,.6);
  }

  .front-shape { position: absolute; inset: 0; }
  .front-mark {
    position: absolute; left: 40px; top: 160px;
    display: flex; align-items: center; gap: 12px;
  }
  .front-mark-name { font-size: 40px; font-weight: 700; color: var(--logo-green); letter-spacing: 1px; }
  .front-mark-dot { width: 30px; height: 30px; border-radius: 50%; background: var(--red); }

  .contact {
    position: absolute; right: 30px; top: 26px;
    text-align: right; color: var(--white);
    font-size: 17px; line-height: 21px;
  }
  .contact-name { font-size: 20px; font-weight: 700; letter-spacing: 1px; }
  .contact-title { font-size: 15px; margin-bottom: 10px; }
  .location { margin-bottom: 4px; }
  .contact-row { display: flex; justify-content: flex-end; align-items: center; gap: 12px; height: 26px; }
  .contact-row:first-of-type { margin-top: 6px; }
  .contact-icon { width: 16px; height: 16px; }
</style>
</head>
<body>
<main class="sheet">

  <section class="card card-back" aria-label="Card back">
    <div class="social" aria-label="Social links">
      <span class="social-dot"></span>
      <span class="social-dot"></span>
    </div>
    <div class="back-mark">
      <span class="back-mark-name">Bru'nettix</span>
      <span class="back-mark-dot"></span>
    </div>
    <p class="back-web">www.brunettix.com</p>
  </section>

  <section class="card card-front" aria-label="Card front">
    <svg class="front-shape" width="700" height="400" viewBox="0 0 700 400">
      <path d="M0 0 H318 C 470 90, 470 330, 290 400 H0 Z" fill="none" stroke="#b3140f" stroke-width="3"/>
      <path d="M0 0 H302 C 452 90, 452 330, 274 400 H0 Z" fill="#ffffff"/>
    </svg>
    <div class="front-mark">
      <span class="front-mark-name">BRU'NETTIX</span>
      <span class="front-mark-dot"></span>
    </div>

    <div class="contact">
      <p class="contact-name">MARA VELTON</p>
      <p class="contact-title">President</p>
      <p class="location">Northvale<br>4087 Corlan Avenue<br>Larkport, OR 97412<br>Phone:360-481-5067</p>
      <p class="location">Cedar Rise<br>7315 Wendmere Road<br>Larkport, OR 97418<br>Phone:360-293-8840</p>
      <div class="contact-row">
        <span>689 502 7714</span>
        <svg class="contact-icon" viewBox="0 0 16 16"><rect x="4" y="1" width="8" height="14" rx="1.5" fill="none" stroke="#fff" stroke-width="1.5"/><circle cx="8" cy="12.5" r="1" fill="#fff"/></svg>
      </div>
      <div class="contact-row">
        <span>name@brunettix.com</span>
        <svg class="contact-icon" viewBox="0 0 16 16"><rect x="1" y="3" width="14" height="10" fill="#fff"/><path d="M1 3 L8 9 L15 3" fill="none" stroke="#2f5b2f" stroke-width="1.2"/></svg>
      </div>
      <div class="contact-row">
        <span>www.brunettix.com</span>
        <svg class="contact-icon" viewBox="0 0 16 16"><circle cx="8" cy="8" r="7" fill="#fff"/><ellipse cx="8" cy="8" rx="3" ry="7" fill="none" stroke="#2f5b2f" stroke-width="1"/><line x1="1" y1="8" x2="15" y2="8" stroke="#2f5b2f" stroke-width="1"/></svg>
      </div>
    </div>
  </section>

</main>
</body>
</html>
```